Lotstallmart.com Webpage Design

Design Brief for lotstallmart.com (Copy of Brief also in attached Word file)

Name of Website- lotstallmart.com (existing logo and look & feel of website to be changed)

Logo - Finalised. The logo files are attached with the brief as “logo.jpeg”. The “Blue- Grey” version of the logo is for use on lighter backgrounds and the “Orange-White” version of the logo is for use on darker backgrounds. (A full Black version of the logo is also attached). Both versions may be used in different parts of the website. All attached files are in .png format.
Status - The website in functional and is undergoing user trials. However, we want to improve the look & feel of the website so at it seems
a. cotemporary,
b. Easy to Navigate
c. professional and
d. Vibrant.

Please visit ‘lotstallmart.com’ to check out the website and its functionalities – please use it only as a reference for the features & functions to be provided, however the designer should use a ‘Free Hand’ in designing the composition of various parts of the webpage without getting too influenced by the existing design

Objective of the Website ‘lotstallmart.com –
a. It is a portal focussed on listing of ‘Retail’ specific real-estate properties by developers, owners and realty brokers. The properties shall listed under the following four categories-
i. Retail Malls
ii. Shopping Complexes
iii. High-street shops
iv. Retail Warehouses
*refer lotstallmart.com for better clarity

b. The abovementioned properties shall be listed either for ‘Sale’ or ‘rent\lease’ or both

c. Users shall visit the site in case they wish to acquire a retail \ shop space either on ‘sale’ or ‘rent’. These Users would be able to specify the ‘Search Criteria’ through the tool-bars provided on the website – the ‘Search Criteria’ shall comprise of ‘Type of space category’, ‘City’, ‘Locality’, transaction type ie ‘Rent \ Sale’ and ‘Area Range’

d. The main revenue model for the website shall be listing fee ( or advertising charges ) payable by those listing their properties on the website.

Three Main Pages of Website (lotstallmart.com) that need to be designed -
a. Main Home Page (visit the web link - http://lotstallmart.com/ ) - The main home page has the “Search Toolbar” for specifying of Search Criteria by the User. It shall also have the following features & functions-
i. Main Advertising Banner
ii. Featured Projects
iii. New Launches
iv. Toolbar with buttons – ‘Advertise with Us’, ‘Listings Alert’, ‘Mart Wizards’, ‘Advertiser Login’

b. Property Listings Page (visit the web link - http://lotstallmart.com/gurgaon-in-india ) - The List of property options that match the Criteria specified by the ‘User’ get displayed on this page.

c. Property Detail Page - When the ‘User’ clicks on the “More….” Button on the ‘Property Listings Page’ (given in point b. above) the web page with the details of the property opens. (For Example – visit the web link - http://lotstallmart.com/vorne-Shopping-Complex-vorne-quadrion-gurgaon-636 )

Note:- Please refer to attached ‘Shopping’ related images the designer may use them on the website to provide a look & feel of retail if required – either separately or rotate in a single window

Target Market(s)

Retailers & Investors looking for retail space, Real Estate Brokers, Developers

Industry/Entity Type

Advertising

Number of Pages Required

3 page

Requirements
Must have
• Refer to existing site lotstallmart.com -- all the existing functionalities are a must have.
Nice to have
• The Designer may use the retail related images on the website if required for making it more vibrant. Refer attached images Shopping(1-6).jpg

```html
<!DOCTYPE html>
<html lang="en">
<head>
<meta charset="utf-8">
<title>Lotstallmart.com – Home</title>
<link rel="stylesheet" href="https://fonts.googleapis.com/css2?family=Quicksand:wght@300;400;500;700&family=PT+Sans:wght@400;700&display=swap">
<style>
:root{
  --orange:#f2a93b;
  --orange-soft:#f6c57c;
  --ink:#333333;
  --muted:#555555;
  --panel:#e3e3e3;
  --panel-light:#f2f2f2;
  --line:#d9d9d9;
  --dark:#2a2727;
  --darker:#1f1d1d;
  --white:#ffffff;
}
*{box-sizing:border-box;margin:0;padding:0}
html,body{width:1200px;height:2927px;overflow:hidden;background:var(--white)}
body{font-family:"PT Sans",Arial,sans-serif;color:var(--ink);position:relative}
.page{position:relative;width:1200px;height:2927px;overflow:hidden}
.abs{position:absolute}

/* hero */
.hero{left:0;top:0;width:1200px;height:520px;background:linear-gradient(180deg,#4a4541 0%,#5a4c40 45%,#3d3733 100%)}
.hero-shade{left:0;top:0;width:1200px;height:520px;background:radial-gradient(ellipse at 50% 45%,rgba(120,100,80,.35),rgba(0,0,0,.35))}
.topnav{left:0;top:0;width:1200px;height:60px}
.nav-item{position:absolute;top:14px;color:var(--white);font-size:14px;line-height:15px;text-align:center;text-transform:uppercase;letter-spacing:.3px}
.nav-sep{position:absolute;top:10px;width:1px;height:38px;background:rgba(255,255,255,.35)}
.btn-register{position:absolute;left:1054px;top:14px;width:110px;height:38px;background:var(--orange);color:var(--white);font-size:13px;line-height:15px;text-align:center;padding-top:4px;text-transform:uppercase}
.welcome{left:0;top:168px;width:1200px;text-align:center;color:var(--white);font-family:"Quicksand",sans-serif;font-size:20px;letter-spacing:1px}
.brand{left:430px;top:208px;width:340px;height:80px;background:rgba(20,18,18,.75);display:flex;align-items:center;justify-content:center;gap:14px}
.brand-dot{width:26px;height:26px;border-radius:50%;background:var(--orange)}
.brand-name{color:var(--white);font-family:"Quicksand",sans-serif;font-weight:700;font-size:34px}
.hero-line{left:599px;top:300px;width:1px;height:80px;background:rgba(255,255,255,.6)}
.scroll-ring{left:575px;top:382px;width:50px;height:50px;border:2px solid rgba(255,255,255,.85);border-radius:50%}

/* search */
.search{left:41px;top:520px;width:1105px;height:368px;background:linear-gradient(180deg,#e8e8e8,#dcdcdc);box-shadow:0 22px 26px -10px rgba(0,0,0,.35)}
.find-title{left:36px;top:18px;font-family:"Quicksand",sans-serif;font-weight:700;font-size:38px;color:var(--orange)}
.find-title em{font-family:"PT Sans",serif;font-style:italic;font-weight:700;color:var(--ink);font-size:24px}
.find-sub{left:36px;top:68px;font-size:18px;color:var(--muted)}
.radio-row{left:36px;top:124px;width:1040px;display:flex}
.radio{display:flex;align-items:center;gap:10px;font-size:16px;text-transform:uppercase;color:var(--ink);width:260px}
.radio-dot{width:18px;height:18px;border:1px solid #777;border-radius:50%;background:var(--white)}
.field{position:absolute;top:194px;width:240px}
.field label{display:block;font-size:12px;text-transform:uppercase;color:var(--ink);margin-bottom:8px}
.select{height:30px;background:var(--white);border:1px solid var(--line);font-size:13px;color:var(--muted);padding:6px 8px;position:relative}
.select::after{content:"";position:absolute;right:0;top:0;width:26px;height:28px;background:var(--orange)}
.select svg{position:absolute;right:7px;top:10px;z-index:1}
.btn-search{left:960px;top:283px;width:114px;height:38px;background:var(--orange);color:var(--white);font-size:16px;text-align:center;line-height:38px;text-transform:uppercase}

/* about */
.section-title-center{left:0;width:1200px;text-align:center;font-family:"Quicksand",sans-serif;font-size:26px;color:var(--ink);letter-spacing:1px}
.about-text{left:130px;top:960px;width:940px;text-align:center;font-size:15px;line-height:24px;color:var(--muted)}
.btn-orange{background:var(--orange);color:var(--white);font-size:16px;text-align:center;text-transform:uppercase}
.divider{left:0;width:1200px;height:2px;background:#ececec}

/* section head */
.section-title{left:51px;font-family:"Quicksand",sans-serif;font-size:30px;color:var(--ink);letter-spacing:1.5px;text-transform:uppercase}
.pager{display:flex;gap:4px}
.pager span{display:block;width:24px;height:24px;background:#e5e5e5;position:relative}
.pager svg{position:absolute;left:7px;top:6px}

/* featured */
.grid{left:51px;top:1256px;width:1095px;height:447px;display:grid;grid-template-columns:repeat(4,1fr);grid-template-rows:repeat(2,1fr)}
.photo{width:100%;height:100%}
.photo-a{background:linear-gradient(160deg,#9cb6cf 0%,#c9c3b6 55%,#8a8373 100%)}
.photo-b{background:linear-gradient(170deg,#5d5a58 0%,#a68f74 50%,#6b625a 100%)}
.photo-c{background:linear-gradient(170deg,#7fa6d0 0%,#d9c7ad 55%,#a86a4c 100%)}
.photo-d{background:linear-gradient(170deg,#e8ecef 0%,#b9b6ae 55%,#77736c 100%)}
.card{background:var(--panel-light);position:relative;padding:16px 18px 0}
.card-type{font-size:13px;font-weight:700;text-transform:uppercase;letter-spacing:1px;color:var(--ink)}
.card-name{font-size:13px;text-transform:uppercase;letter-spacing:1px;color:var(--muted);margin-top:8px}
.card-desc{font-size:12.5px;line-height:18px;color:var(--muted);margin-top:14px}
.card-bar{position:absolute;left:0;bottom:0;width:100%;height:40px;display:flex;font-size:13px;text-transform:uppercase;letter-spacing:.5px}
.card-bar .deal{flex:1;background:#e2e2e2;color:var(--ink);line-height:40px;padding-left:18px}
.card-bar .more{width:150px;background:var(--orange-soft);color:var(--white);line-height:40px;text-align:center}

/* new launch */
.launch{left:56px;top:1846px;width:1081px;height:330px;background:var(--panel-light)}
.launch-photo{left:0;top:0;width:583px;height:330px;background:linear-gradient(175deg,#3f3a36 0%,#8e7760 45%,#c9b69a 70%,#6b5f52 100%)}
.launch-tag{left:0;top:0;width:310px;height:68px;background:var(--orange);color:var(--white);font-family:"Quicksand",sans-serif;font-weight:700;font-size:30px;line-height:68px;padding-left:24px;text-transform:uppercase}
.launch-name{left:620px;top:44px;font-family:"Quicksand",sans-serif;font-weight:700;font-size:30px;text-transform:uppercase;color:var(--ink)}
.launch-deal{left:620px;top:96px;font-family:"Quicksand",sans-serif;font-weight:500;font-size:22px;letter-spacing:1px;color:var(--ink)}
.launch-desc{left:620px;top:156px;width:430px;font-size:15px;line-height:24px;color:var(--muted)}
.launch-state{left:583px;top:250px;width:244px;height:80px;background:var(--orange-soft);color:var(--ink);font-family:"Quicksand",sans-serif;font-weight:700;font-size:19px;line-height:80px;text-align:center;text-transform:uppercase}
.launch-area{left:827px;top:250px;width:254px;height:80px;background:#ececec;color:var(--ink);font-family:"Quicksand",sans-serif;font-weight:700;font-size:21px;line-height:80px;text-align:center}

/* alert */
.alert{left:0;top:2244px;width:1200px;height:244px;background:var(--dark)}
.alert-title{left:0;top:42px;width:1200px;text-align:center;font-family:"Quicksand",sans-serif;font-size:28px;letter-spacing:3px;color:var(--orange);text-transform:uppercase}
.alert-sub{left:0;top:86px;width:1200px;text-align:center;font-family:"Quicksand",sans-serif;font-weight:500;font-size:22px;letter-spacing:1.5px;color:var(--white);text-transform:uppercase}
.alert-form{left:142px;top:137px;display:flex;gap:14px}
.input{width:230px;height:36px;background:#e5e5e5;font-size:13px;color:#666;padding:9px 10px;position:relative}
.input.dd::after{content:"";position:absolute;right:0;top:0;width:28px;height:36px;background:#b5b5b5}
.input.dd svg{position:absolute;right:9px;top:14px;z-index:1}
.btn-subscribe{width:170px;height:36px;background:var(--orange);color:var(--white);font-size:16px;line-height:36px;text-align:center;text-transform:uppercase}

/* partners */
.partners{left:0;top:2488px;width:1200px;height:146px}
.p-arrow{position:absolute;top:56px;width:30px;height:30px;border:2px solid #888;border-radius:50%}
.p-arrow svg{position:absolute;left:7px;top:7px}
.p-row{position:absolute;left:137px;top:40px;display:flex;gap:46px}
.p-box{width:110px;height:66px;border:1px solid #dcdcdc;background:#fafafa;display:flex;align-items:center;justify-content:center}
.p-box i{display:block;width:70px;height:26px;background:#c9cfd8}
.p-box.photo-tile{background:linear-gradient(170deg,#6f7d96,#a49b8f)}

/* footer */
.footer{left:0;top:2634px;width:1200px;height:293px;background:var(--darker);color:#d9d9d9}
.f-head{position:absolute;top:32px;font-size:18px;color:var(--white);text-transform:uppercase;letter-spacing:.5px}
.f-text{position:absolute;font-size:14px;line-height:21px;color:#cfcfcf}
.f-input{position:absolute;left:512px;width:228px;height:32px;background:#5a5757;color:#cfcfcf;font-size:12px;padding:8px 10px}
.f-input.dd::after{content:"";position:absolute;right:0;top:0;width:26px;height:32px;background:#6e6b6b}
.f-btn{position:absolute;background:var(--orange);color:var(--white);text-align:center}
.contact-line{position:absolute;left:902px;display:flex;gap:12px;font-size:14px;line-height:21px;color:#cfcfcf}
</style>
</head>
<body>
<div class="page">

  <!-- hero -->
  <div class="abs hero" role="img" aria-label="Photo of shoppers walking through a busy retail mall"></div>
  <div class="abs hero-shade"></div>
  <nav class="abs topnav">
    <div class="nav-item" style="left:38px;width:70px">Advertise<br><span style="text-transform:none">with us</span></div>
    <div class="nav-sep" style="left:262px"></div>
    <div class="nav-item" style="left:370px;width:70px">Listings<br>Alert</div>
    <div class="nav-sep" style="left:640px"></div>
    <div class="nav-item" style="left:730px;width:70px">Mart<br><span style="text-transform:none">Wizards</span></div>
    <div class="nav-sep" style="left:1050px"></div>
    <div class="btn-register">Advertiser<br>Register</div>
  </nav>
  <div class="abs welcome">Welcome to</div>
  <div class="abs brand"><span class="brand-dot"></span><span class="brand-name">lotstallmart</span></div>
  <div class="abs hero-line"></div>
  <div class="abs scroll-ring">
    <svg width="46" height="46" viewBox="0 0 46 46"><path d="M17 20l6 6 6-6" fill="none" stroke="#fff" stroke-width="2"/></svg>
  </div>

  <!-- search -->
  <section class="abs search">
    <div class="abs find-title">FIND <em>a location</em></div>
    <div class="abs find-sub">Looking for stylish, modern space in a prime city center location?&nbsp; We have the ideal solution...</div>
    <div class="abs radio-row">
      <div class="radio"><svg width="18" height="18" viewBox="0 0 18 18"><path d="M3 9l4 4 8-9" fill="none" stroke="#333" stroke-width="2.2"/></svg>Retail Malls</div>
      <div class="radio" style="width:270px"><span class="radio-dot"></span>Shopping Complexes</div>
      <div class="radio" style="width:270px"><span class="radio-dot"></span>High-Street Shops</div>
      <div class="radio"><span class="radio-dot"></span>Retail Warehouses</div>
    </div>
    <div class="field" style="left:36px"><label>Select State/County</label><div class="select">Bangalore<svg width="12" height="8" viewBox="0 0 12 8"><path d="M1 1l5 5 5-5" fill="none" stroke="#fff" stroke-width="2"/></svg></div></div>
    <div class="field" style="left:302px"><label>Select Locality/Micro Market</label><div class="select">Select<svg width="12" height="8" viewBox="0 0 12 8"><path d="M1 1l5 5 5-5" fill="none" stroke="#fff" stroke-width="2"/></svg></div></div>
    <div class="field" style="left:568px"><label>Transaction Type</label><div class="select">Rent<svg width="12" height="8" viewBox="0 0 12 8"><path d="M1 1l5 5 5-5" fill="none" stroke="#fff" stroke-width="2"/></svg></div></div>
    <div class="field" style="left:834px"><label>Enter Keywords</label><div class="select">Project name, Developers<svg width="12" height="8" viewBox="0 0 12 8"><path d="M1 1l5 5 5-5" fill="none" stroke="#fff" stroke-width="2"/></svg></div></div>
    <div class="abs btn-search">Search</div>
  </section>

  <!-- about -->
  <h2 class="abs section-title-center" style="top:918px">ABOUT US!</h2>
  <p class="abs about-text">Lotstallmart.com - About Us Lotstallmart.com is a Specialised Web based platform for Retail Space, featuring properties across India under various formats such as Retail Malls, Shopping Complexes, High-street Shops. Lotstallmart.com is useful to various category of users as follows Developers, Retailers, Investors, Brokers.</p>
  <div class="abs btn-orange" style="left:564px;top:1069px;width:114px;height:38px;line-height:38px">Read More</div>
  <div class="abs divider" style="top:1142px"></div>

  <!-- featured -->
  <h2 class="abs section-title" style="top:1175px">Featured Projects</h2>
  <div class="abs pager" style="left:1084px;top:1182px">
    <span><svg width="10" height="12" viewBox="0 0 10 12"><path d="M7 1L2 6l5 5" fill="none" stroke="#777" stroke-width="2"/></svg></span>
    <span><svg width="10" height="12" viewBox="0 0 10 12"><path d="M3 1l5 5-5 5" fill="none" stroke="#777" stroke-width="2"/></svg></span>
  </div>
  <div class="abs grid">
    <div class="photo photo-a" role="img" aria-label="Photo of a modern shopping complex building"></div>
    <div class="card">
      <div class="card-type">Shopping Complex</div>
      <div class="card-name">Corvane Atrium</div>
      <div class="card-desc">Kestrel Developers presents sustainable modern retail cum office complexes, developed to fulfill the requirements of modern and dynamic businesses.</div>
      <div class="card-bar"><span class="deal">Sale / Rent</span><span class="more">More Details</span></div>
    </div>
    <div class="photo photo-b" role="img" aria-label="Photo of a multi-level mall atrium"></div>
    <div class="card">
      <div class="card-type">Shopping Complex</div>
      <div class="card-name">Lumera 81 High Street</div>
      <div class="card-desc">100 meters away from Faridabad's most affluent residential sectors 14 -17." At the absolute Entrance of Greater Faridabad in Sector 81.</div>
      <div class="card-bar"><span class="deal">Sale / Rent</span><span class="more">More Details</span></div>
    </div>
    <div class="card">
      <div class="card-type">Shopping Complex</div>
      <div class="card-name">The Cobalt Court</div>
      <div class="card-desc">Operational Complex with good quality retailers and assured footfalls on Main Sohna Road...</div>
      <div class="card-bar"><span class="deal">Sale / Rent</span><span class="more">More Details</span></div>
    </div>
    <div class="photo photo-c" role="img" aria-label="Photo of a shopping complex facade under a blue sky"></div>
    <div class="card">
      <div class="card-type">Shopping Complex</div>
      <div class="card-name">The Cobalt Court</div>
      <div class="card-desc">Operational Complex with good quality retailers and assured footfalls on Main Sohna Road...</div>
      <div class="card-bar"><span class="deal">Sale / Rent</span><span class="more">More Details</span></div>
    </div>
    <div class="photo photo-d" role="img" aria-label="Photo of an open-air retail plaza with a glass canopy"></div>
  </div>
  <div class="abs divider" style="top:1751px"></div>

  <!-- new launches -->
  <h2 class="abs section-title" style="top:1783px">New Launches</h2>
  <div class="abs pager" style="left:1084px;top:1790px">
    <span><svg width="10" height="12" viewBox="0 0 10 12"><path d="M7 1L2 6l5 5" fill="none" stroke="#777" stroke-width="2"/></svg></span>
    <span><svg width="10" height="12" viewBox="0 0 10 12"><path d="M3 1l5 5-5 5" fill="none" stroke="#777" stroke-width="2"/></svg></span>
  </div>
  <article class="abs launch">
    <div class="abs launch-photo" role="img" aria-label="Photo of a retail mall concourse with shopfronts"></div>
    <div class="abs launch-tag">Retail Malls</div>
    <div class="abs launch-name">Tidal One</div>
    <div class="abs launch-deal">SALE / RENT</div>
    <p class="abs launch-desc">100 meters away from Faridabad's most affluent residential sectors 14 -17." At the absolute Entrance of Greater Faridabad in Sector 81.</p>
    <div class="abs launch-state">Uttar Pradesh</div>
    <div class="abs launch-area">745 SQ.FT</div>
  </article>

  <!-- listing alert -->
  <section class="abs alert">
    <h2 class="abs alert-title">Listing Alert</h2>
    <div class="abs alert-sub">Suscribe&nbsp; for fortnightly email update on new listings @ lotstallmart</div>
    <div class="abs alert-form">
      <div class="input">Enter email address</div>
      <div class="input dd">Select options<svg width="10" height="7" viewBox="0 0 10 7"><path d="M1 1l4 4 4-4" fill="none" stroke="#fff" stroke-width="2"/></svg></div>
      <div class="input dd">Select City<svg width="10" height="7" viewBox="0 0 10 7"><path d="M1 1l4 4 4-4" fill="none" stroke="#fff" stroke-width="2"/></svg></div>
      <div class="btn-subscribe">Suscribe</div>
    </div>
  </section>

  <!-- partners -->
  <section class="abs partners">
    <div class="p-arrow" style="left:56px"><svg width="12" height="12" viewBox="0 0 12 12"><path d="M11 6H2M6 2L2 6l4 4" fill="none" stroke="#777" stroke-width="1.6"/></svg></div>
    <div class="p-row">
      <div class="p-box photo-tile" role="img" aria-label="Thumbnail photo of a retail building"></div>
      <div class="p-box"><i></i></div>
      <div class="p-box"><i style="width:40px;height:50px"></i></div>
      <div class="p-box"><i style="width:50px"></i></div>
      <div class="p-box"><i style="width:60px;height:40px;border-radius:50%"></i></div>
      <div class="p-box"><i></i></div>
      <div class="p-box photo-tile" role="img" aria-label="Thumbnail photo of a retail building"></div>
    </div>
    <div class="p-arrow" style="left:1094px"><svg width="12" height="12" viewBox="0 0 12 12"><path d="M1 6h9M6 2l4 4-4 4" fill="none" stroke="#777" stroke-width="1.6"/></svg></div>
  </section>

  <!-- footer -->
  <footer class="abs footer">
    <div class="f-head" style="left:73px">Editor's Choice</div>
    <p class="f-text" style="left:73px;top:68px;width:360px">A "Select" Listing of Retail Properties Handpicked by our Editors based on their own positive evaluation on parameters &amp; attributes such as Design Concept, Location, Developer, Success Potential. So Read On to Check Out for yourself</p>
    <div class="f-btn" style="left:78px;top:200px;width:64px;height:28px;line-height:28px;font-size:14px">MORE</div>

    <div class="f-head" style="left:512px">Email Update</div>
    <p class="f-text" style="left:512px;top:68px;width:260px;font-size:13px;line-height:19px">Suscribe&nbsp; for Fortnightly Email update on New Listings @ Lotstallmart</p>
    <div class="f-input" style="top:114px">Enter email address</div>
    <div class="f-input dd" style="top:156px">Select City</div>
    <div class="f-input dd" style="top:198px">Select options</div>
    <div class="f-btn" style="left:512px;top:240px;width:80px;height:26px;line-height:26px;font-size:12px">Subscribe</div>

    <div class="f-head" style="left:902px">Contact</div>
    <div class="contact-line" style="top:82px">
      <svg width="12" height="18" viewBox="0 0 12 18"><path d="M6 0a6 6 0 0 0-6 6c0 4.5 6 12 6 12s6-7.5 6-12a6 6 0 0 0-6-6zm0 8.5A2.5 2.5 0 1 1 6 3.5a2.5 2.5 0 0 1 0 5z" fill="#cfcfcf"/></svg>
      <span>Nexa Retail Hub, Unit 212, 2nd Floor,<br>Lorem Ipsum is simply,<br>Sector-x, Gurgaon - 122002</span>
    </div>
    <div class="contact-line" style="top:162px">
      <svg width="16" height="16" viewBox="0 0 16 16"><path d="M3 1h3l1.5 4-2 1.2a9 9 0 0 0 4.3 4.3L11 8.5l4 1.5v3c0 1-1 2-2 2C6.4 15 1 9.6 1 3c0-1 1-2 2-2z" fill="#cfcfcf"/></svg>
      <span>Phone : 000-000-0000</span>
    </div>
    <p class="f-text" style="left:934px;top:236px;width:220px;font-size:11px;line-height:14px;color:#a9a9a9">Copyright © 2015 Nexa Retail Hub.com.<br>All rights reserved.</p>
  </footer>

</div>
</body>
</html>
```